Elegant Business Card for Technology Company

Client is a supplier of innovative industrial communications and automation equipment since 2002. This contest is to gather fresh ideas for a redesign of the existing business card. Client is looking for design that best communicates tagline "Industrial Networking and Computing Specialist".

Design submissions should look modern, clean, elegant and professional. It should not be cluttered. Use white as the primary colour. Orange and black as secondary colour. Refer to jpeg File 1 on the current design.

Fonts used by Client used include Arial Regular, Arial Black, Roboto Regular, Roboto Black and Lato.

The winning design will be sent for offset printing using super white 250gsm artcard paper (open for suggestions).

Target Market(s)

System Engineers, Project Managers, Purchasing Managers from companies providing engineering services for Smart Cities.

Industry/Entity Type

Information Technology

Contact Information for Business Card

Refer to PDF File 3 for Business Card Details. Priority of short contact information would be as follows Name > Job Title > Email > Mobile > Web > Tel > Fax > Business Address >UEN (UEN represents company registration number)

Font styles to use
Sans Serif

Colors
ffffff
f37122
000000
5c5c5c

Requirements
Must have
• Refer to AI File 2 (Company Logo) & PDF File 3 (Information on Namecard)
Should not have
• No QR codes
• No Social Media Icons
• Do not create full Black or Orange colour background

```html
<!DOCTYPE html>
<html lang="en">
<head>
<meta charset="utf-8">
<title>Norvex Business Card</title>
<link rel="stylesheet" href="https://fonts.googleapis.com/css2?family=Roboto:wght@400;700;900&display=swap">
<style>
  :root {
    --white: #ffffff;
    --orange: #f37122;
    --black: #000000;
    --grey: #5c5c5c;
    --charcoal: #1e1e1e;
    --stage: #3b3b3b;
  }
  * { box-sizing: border-box; margin: 0; padding: 0; }
  html, body { width: 1200px; height: 900px; overflow: hidden; }
  body {
    background: var(--stage);
    font-family: "Roboto", Arial, sans-serif;
    position: relative;
  }
  .card {
    position: absolute;
    left: 280px;
    width: 640px;
    height: 366px;
    border-radius: 22px;
    overflow: hidden;
  }
  .card--back {
    top: 50px;
    background: linear-gradient(135deg, var(--charcoal) 0%, #0d0d0d 45%, var(--black) 75%);
    color: var(--white);
  }
  .card--front { top: 484px; background: var(--white); color: var(--black); }

  .brand {
    position: absolute;
    display: flex;
    align-items: center;
  }
  .brand__dot {
    border-radius: 50%;
    background: var(--orange);
    flex: none;
  }
  .brand__name {
    font-weight: 900;
    line-height: 1;
    white-space: nowrap;
  }
  .card--back .brand { left: 50px; top: 128px; gap: 12px; }
  .card--back .brand__dot { width: 42px; height: 42px; }
  .card--back .brand__name { font-size: 44px; color: var(--white); }
  .card--front .brand { left: 50px; top: 96px; gap: 14px; }
  .card--front .brand__dot { width: 54px; height: 54px; }
  .card--front .brand__name { font-size: 60px; letter-spacing: 1px; color: var(--black); }

  .back__texture {
    position: absolute;
    right: 0; top: 0;
    width: 340px; height: 270px;
    background: radial-gradient(ellipse at 60% 40%, #4a2a14 0%, #24150b 40%, rgba(0,0,0,0) 75%);
  }
  .services {
    position: absolute;
    left: 352px; top: 112px;
    list-style: none;
    font-size: 14.5px;
    line-height: 1.45;
    white-space: nowrap;
  }
  .tagline {
    position: absolute;
    left: 50px; bottom: 34px;
    color: var(--orange);
    font-size: 16px;
    letter-spacing: 0.3px;
    text-transform: uppercase;
  }

  .company {
    position: absolute;
    left: 50px; top: 172px;
    font-size: 17px;
    text-transform: uppercase;
    color: var(--black);
  }
  .company__short { color: var(--orange); font-weight: 700; }

  .person {
    position: absolute;
    left: 410px; top: 60px;
  }
  .person__name { font-size: 22px; font-weight: 900; text-transform: uppercase; letter-spacing: 0.5px; }
  .person__title { font-size: 14px; color: var(--orange); text-transform: uppercase; letter-spacing: 0.5px; margin-top: 2px; }
  .contacts { list-style: none; margin-top: 12px; }
  .contacts li {
    display: flex; align-items: center; gap: 10px;
    font-size: 14px; line-height: 21px; color: var(--black);
  }
  .contacts svg { width: 12px; height: 12px; flex: none; }

  .front__bands { position: absolute; inset: 0; width: 640px; height: 366px; }
  .address {
    position: absolute;
    left: 36px; bottom: 8px;
    color: var(--white);
    font-size: 14px;
    font-style: normal;
    line-height: 1.3;
  }
  .uen {
    position: absolute;
    right: 26px; top: 252px;
    color: var(--white);
    font-size: 15px;
  }
</style>
</head>
<body>

<section class="card card--back" aria-label="Business card back">
  <div class="back__texture" role="img" aria-label="Soft dark orange decorative texture"></div>
  <div class="brand">
    <span class="brand__dot"></span>
    <span class="brand__name">NORVEX</span>
  </div>
  <ul class="services">
    <li>Industrial Ethernet / Wireless / Cellular</li>
    <li>Industrial and Embedded Computing</li>
    <li>Serial / Fieldbus Connectivity</li>
    <li>IP Video Surveillance</li>
    <li>Remote Automation</li>
  </ul>
  <p class="tagline">Industrial Networking and Computing Specialist</p>
</section>

<section class="card card--front" aria-label="Business card front">
  <svg class="front__bands" viewBox="0 0 640 366" aria-hidden="true">
    <polygon points="405,246 640,246 640,280 378,280" fill="var(--orange)"/>
    <polygon points="0,316 348,316 378,280 640,280 640,366 0,366" fill="var(--black)"/>
  </svg>

  <div class="brand">
    <span class="brand__dot"></span>
    <span class="brand__name">NORVEX</span>
  </div>
  <p class="company"><span class="company__short">Norvex</span> Asia Pacific Pte Ltd</p>

  <div class="person">
    <h1 class="person__name">Daniel Loh</h1>
    <p class="person__title">Sales Manager</p>
    <ul class="contacts">
      <li>
        <svg viewBox="0 0 12 12"><rect x="3" y="0.5" width="6" height="11" rx="1" fill="none" stroke="var(--orange)" stroke-width="1.2"/><circle cx="6" cy="9.5" r="0.7" fill="var(--orange)"/></svg>
        +65 8123 4567
      </li>
      <li>
        <svg viewBox="0 0 12 12"><path d="M2.5 1 L4.5 1 L5.3 3.6 L4 4.6 Q5 7 7.4 8 L8.4 6.7 L11 7.5 L11 9.5 Q10.5 11 9 11 Q1 10 1 2.5 Q1 1 2.5 1 Z" fill="var(--orange)"/></svg>
        +65 6555 0140
      </li>
      <li>
        <svg viewBox="0 0 12 12"><rect x="3" y="1" width="6" height="4" fill="none" stroke="var(--orange)" stroke-width="1.2"/><rect x="1" y="5" width="10" height="5" rx="1" fill="var(--orange)"/></svg>
        +65 6555 0183
      </li>
      <li>
        <svg viewBox="0 0 12 12"><rect x="0.8" y="2.3" width="10.4" height="7.4" fill="none" stroke="var(--orange)" stroke-width="1.2"/><path d="M1 2.7 L6 6.5 L11 2.7" fill="none" stroke="var(--orange)" stroke-width="1.2"/></svg>
        sales@norvex.com.sg
      </li>
      <li>
        <svg viewBox="0 0 12 12"><circle cx="6" cy="6" r="5" fill="none" stroke="var(--orange)" stroke-width="1.2"/><ellipse cx="6" cy="6" rx="2.2" ry="5" fill="none" stroke="var(--orange)" stroke-width="1"/><line x1="1" y1="6" x2="11" y2="6" stroke="var(--orange)" stroke-width="1"/></svg>
        www.norvex.com.sg
      </li>
    </ul>
  </div>

  <p class="uen">UEN No: 200299999K</p>
  <address class="address">8 Kallang Way Tech Hub #02-15<br>(Lobby B), Singapore 349999</address>
</section>

</body>
</html>
```